KorvaNest - Home Income and Business Resources Platform

I am looking for a website template for a multi-purposed website. This website will feature:

1.) Website Directory with Ratings & comments on listings
2.) Company Blog
3.) Homepage with Content (see files for homepage mock)

I would like the Design to have a default width 1170px (wider then normal)

Of course I am looking for Pages for Listings to be designed.

Great looking BLOG Layout: http://journal.plimworks.example/html/blog.html

I would like 4 Versions of a Website Directory Listing "Box"
1.) Basic Listing Box
2.) Sponsored Listing Box
3.) Recommended Listing Box
4.) Stay Away From Listing Box

Information on the Listing Page (Like on a Category Page)
Site Name, Site URL, Website Image, # of Views, Rating and # of Comments

Information on the Listing Details Page:
Same as ABOVE + About website Description, Vornic Score, Category Information

Decent looking examples is here: https://samples.trevolin.example/directory/computers/ and http://www.zqrankhub.example/.

I will include some sketches and screenshots of things I like/looking for. As designers,you have creative freedom and are encouraged to show this. This is Phase one of this project and winning designer is guaranteed to have future work for this project.

Target Market(s)

Directory, business, websites

Industry/Entity Type

Business

Coding

Coded - Design and coding required

Number of Pages Required

5+ page

Font styles to use
Sans Serif

Colors

Designer to choose colors to be used in the design.

Requirements
Must have
• Professional yet clean look. The use of Icons & images
• Unique Look
Should not have
• Any exact copies of any examples I provided

```html
<!DOCTYPE html>
<html lang="en">
<head>
<meta charset="utf-8">
<title>KorvaNest – Home Income &amp; Business Resources</title>
<link rel="stylesheet" href="https://fonts.googleapis.com/css2?family=Lato:wght@700;900&family=Open+Sans:wght@400;600&display=swap">
<style>
:root{
  --orange:#f0862a;
  --ink:#2b2b2b;
  --text:#555;
  --blue:#1279c9;
  --blue-link:#1a7cc6;
  --red:#d14343;
  --green:#4d9f1c;
  --page:#f1f1f1;
  --line:#e2e2e2;
  --footer:#242424;
}
*{box-sizing:border-box;margin:0;padding:0}
html,body{width:1200px;height:951px;overflow:hidden}
body{background:var(--page);font-family:"Open Sans",sans-serif;color:var(--text);position:relative}
.site-header{position:absolute;left:0;top:0;width:1200px;height:81px;background:#fff;border-top:3px solid var(--orange);box-shadow:0 1px 3px rgba(0,0,0,.12)}
.brand{position:absolute;left:97px;top:30px;font:900 23px "Lato",sans-serif;color:var(--ink);letter-spacing:.3px}
.main-nav{position:absolute;left:330px;top:34px;display:flex;gap:0;font:700 15px "Lato",sans-serif;color:var(--ink)}
.main-nav span{position:absolute;white-space:nowrap}
.main-nav .active{color:var(--orange)}
.search-icon{position:absolute;left:987px;top:36px}
.login{position:absolute;left:1021px;top:24px;width:80px;height:35px;border:1px solid #bbb;color:var(--orange);font:700 15px "Lato",sans-serif;display:flex;align-items:center;justify-content:center;gap:6px}
.hero{position:absolute;left:99px;top:166px;width:759px;height:265px;background:#fff;border:1px solid #ddd;padding:2px}
.hero-photo{position:absolute;left:2px;top:2px;width:753px;height:259px;background:linear-gradient(90deg,#c9a990 0%,#d8c2b0 25%,#e9e3dd 42%,#f6f4f1 55%,#f4f2ef 80%,#ece7e1 100%)}
.hero-copy{position:absolute;left:330px;top:27px;width:400px}
.hero-copy h1{font:900 22px "Lato",sans-serif;color:var(--ink);letter-spacing:.1px}
.hero-copy h2{margin-top:10px;font:600 16px "Open Sans",sans-serif;color:var(--blue-link)}
.hero-copy p{margin-top:12px;font-size:12.5px;line-height:22.3px;color:#666}
.btn-outline{display:inline-block;margin-top:14px;width:94px;height:31px;border:1px solid #aaa;color:var(--orange);font:700 12.5px "Lato",sans-serif;text-align:center;line-height:29px}
.feature{position:absolute;top:458px;width:238px;height:348px;color:#fff}
.feature.blue{left:99px;background:var(--blue)}
.feature.red{left:359px;background:var(--red)}
.feature.green{left:620px;background:var(--green)}
.feature-photo{position:absolute;left:3px;top:3px;width:232px;height:137px}
.blue .feature-photo{background:linear-gradient(135deg,#e9e6e6,#cfc8c8 60%,#b9b3b3)}
.red .feature-photo{background:linear-gradient(135deg,#e8b16e,#a96a3c 55%,#3e2b22)}
.green .feature-photo{background:linear-gradient(135deg,#7ea0cc,#4064a0 55%,#c2d3ea)}
.feature-head{position:absolute;left:17px;top:155px;display:flex;align-items:center;gap:10px;font:700 14px/17px "Lato",sans-serif;text-transform:uppercase}
.feature-rule{position:absolute;left:17px;right:26px;top:207px;border-top:1px solid rgba(255,255,255,.55)}
.feature p{position:absolute;left:17px;top:221px;width:212px;font-size:12.5px;line-height:21.5px}
.feature .more{position:absolute;left:17px;top:318px;font:700 12.5px "Lato",sans-serif}
.sponsored{position:absolute;left:887px;top:166px;width:214px;height:389px;background:#fff;border:1px solid #ddd}
.sponsored h3{height:50px;background:var(--orange);color:#fff;font:900 20px/50px "Lato",sans-serif;padding-left:21px;margin:-1px -1px 0}
.sponsor{position:absolute;left:13px;width:188px;display:flex;align-items:center;gap:10px;font-size:13.5px;color:#333}
.sponsor + .sponsor{}
.sponsor .mark{width:84px;font:700 18px "Lato",sans-serif;color:var(--blue)}
.sponsor-rule{position:absolute;left:13px;width:188px;border-top:1px solid var(--line)}
.promo{position:absolute;left:887px;top:591px;width:214px;height:215px;background:#fff;border:1px solid #ddd;padding:2px}
.promo-art{width:100%;height:100%;background:linear-gradient(180deg,#f1ebdd,#e6dcc6 70%,#c46a2c 88%,#b85f24)}
.site-footer{position:absolute;left:0;top:884px;width:1200px;height:67px;background:var(--footer);color:#eee;font-size:13px;text-align:center;line-height:67px}
</style>
</head>
<body>
<header class="site-header">
  <div class="brand">KORVANEST</div>
  <nav class="main-nav">
    <span class="active" style="left:0">HOME</span>
    <span style="left:76px">ABOUT US</span>
    <span style="left:181px">RESOURCES</span>
    <span style="left:296px">BUSINESS DIRECTORY</span>
    <span style="left:482px">NEWS</span>
    <span style="left:556px">CONTACT</span>
  </nav>
  <svg class="search-icon" width="15" height="15" viewBox="0 0 15 15"><circle cx="6" cy="6" r="4.5" fill="none" stroke="#2b2b2b" stroke-width="2"/><line x1="9.3" y1="9.3" x2="13.5" y2="13.5" stroke="#2b2b2b" stroke-width="2.2" stroke-linecap="round"/></svg>
  <div class="login"><svg width="10" height="12" viewBox="0 0 10 12"><path d="M2.5 5V3.5a2.5 2.5 0 0 1 5 0V5" fill="none" stroke="#f0862a" stroke-width="1.5"/><rect x="0.5" y="5" width="9" height="7" rx="1" fill="#f0862a"/></svg>LOGIN</div>
</header>

<section class="hero">
  <div class="hero-photo" role="img" aria-label="Smiling couple on a sofa using a laptop at home"></div>
  <div class="hero-copy">
    <h1>ABOUT KORVANEST</h1>
    <h2>We are Home Income &amp; Business resources directory.</h2>
    <p>At vero eos et accusamus et iusto odio dignissimos ducimus qui bland itiis praesentium voluptatum deleniti atque corrupti quos dolores etqu as molestias excepturi sint occaecati cupiditate non provident, simique sunt in culpa qui officia deserunt moll.</p>
    <span class="btn-outline">READ MORE</span>
  </div>
</section>

<article class="feature blue">
  <div class="feature-photo" role="img" aria-label="Small house model, key and pen on paperwork"></div>
  <div class="feature-head">
    <svg width="30" height="36" viewBox="0 0 30 36"><path d="M1 1h19l9 9v25H1z" fill="#fff"/><path d="M20 1v9h9" fill="#cfe3f5"/><g stroke="#1279c9" stroke-width="2"><line x1="8" y1="18" x2="22" y2="18"/><line x1="8" y1="23" x2="22" y2="23"/><line x1="8" y1="28" x2="22" y2="28"/></g></svg>
    <span>Home Income<br>Resource Directory</span>
  </div>
  <div class="feature-rule"></div>
  <p>Find what you need, when you need it.The KorvaNest website directory is your one-stop pit for anything involved in making money</p>
  <span class="more">LEARN MORE</span>
</article>

<article class="feature red">
  <div class="feature-photo" role="img" aria-label="Hands pointing at a tablet and papers on a desk"></div>
  <div class="feature-head">
    <svg width="46" height="32" viewBox="0 0 46 32"><rect x="6" y="2" width="34" height="22" rx="2" fill="none" stroke="#fff" stroke-width="2.5"/><path d="M1 27h44v2a2 2 0 0 1-2 2H3a2 2 0 0 1-2-2z" fill="#fff"/></svg>
    <span>Advertising<br>Benefits</span>
  </div>
  <div class="feature-rule"></div>
  <p>Everyone needs to advertise and we know just how to get your offer out to the right people. We have many methods including</p>
  <span class="more">LEARN MORE</span>
</article>

<article class="feature green">
  <div class="feature-photo" role="img" aria-label="Hand touching a rising bar and line chart"></div>
  <div class="feature-head">
    <svg width="26" height="44" viewBox="0 0 26 44"><line x1="13" y1="1" x2="13" y2="43" stroke="#fff" stroke-width="3"/><path d="M22 12c-2-3-5-4-9-4-5 0-8 2.5-8 6 0 8 17 5 17 14 0 4-4 7-9 7-4 0-8-2-10-5" fill="none" stroke="#fff" stroke-width="4.5" stroke-linecap="round"/></svg>
    <span>Earning with<br>KorvaNest</span>
  </div>
  <div class="feature-rule"></div>
  <p>Text: Join KorvaNest and start earning money. When you share KorvaNest and lock in an advertiser or premium listing, we reward you.</p>
  <span class="more">LEARN MORE</span>
</article>

<aside class="sponsored">
  <h3>SPONSORED</h3>
  <div class="sponsor" style="top:73px"><span class="mark">Tarnell</span>Lorem ipsum</div>
  <div class="sponsor-rule" style="top:130px"></div>
  <div class="sponsor" style="top:158px"><span class="mark">Quorvik</span>Lorem ipsum</div>
  <div class="sponsor-rule" style="top:226px"></div>
  <div class="sponsor" style="top:252px"><span class="mark">Mendra</span>Lorem ipsum</div>
  <div class="sponsor-rule" style="top:310px"></div>
  <div class="sponsor" style="top:330px"><span class="mark">Holbe</span>Lorem ipsum</div>
</aside>

<aside class="promo">
  <div class="promo-art" role="img" aria-label="Home equity advertisement with a house frame made of tools"></div>
</aside>

<footer class="site-footer">Copyright © 2017. KorvaNest. All Rights Reserved.</footer>
</body>
</html>
```